Business card for a new innovative and professional lawn care business

We need a business card design for a new lawn care business in Halifax NS Canada. We offer lawn services in Halifax & Bedford. Our services offered include lawn care, garden services, and property maintenance. We take pride in our work and are experienced at what we do. I would like to see a design that is double sided. On the backside I would like the something simple (maybe my logo preferably on blackround (linked below) with website link, Facebook page or something). The front I want to include contact info:
Morgan Pell
phone 902-555-0148
email - brookvaleyards.ca
facebook - Facebook.com/brookvaleyards
Instagram maybe ? - instagram.com/brookvaleyard
Serving Halifax and Bedford for 5 years?
I don't want it to have too much information as I will be passing them out in aim to visit website, or call !
We do want it to include lawn care, garden services and property maintenance.
Basic, catchy, and modern looking !
Logo attached below !

Target Market(s)

Passing business cards to everyone I meet or interact with.

Industry/Entity Type

Lawn Care

Contact Information for Business Card

Double sided with some basic information, with catchy colours and easy to look at.

Font styles to use
Sans Serif

Requirements
Must have
• Must be double sided and have :
• Name, Phone, Email, FB, Website, and 3 main services offered - lawn care, property maintenance, garden services
Nice to have
• Would be nice to have instagram link if it goes well on there
Should not have
• Don't want too much writing or images that are distracting

```html
<!DOCTYPE html>
<html lang="en">
<head>
<meta charset="utf-8">
<title>Brookvale Yards — Business Card</title>
<link rel="stylesheet" href="https://fonts.googleapis.com/css2?family=Open+Sans:wght@400;600;700&display=swap">
<style>
  :root {
    --page: #ecebe6;
    --card: #ffffff;
    --green-dark: #0b6b3a;
    --green-mid: #2e8b3f;
    --green-light: #8cc63f;
    --text: #3b3b3b;
    --rule: #e2e2e2;
  }
  * { box-sizing: border-box; margin: 0; padding: 0; }
  html, body { width: 1200px; height: 950px; overflow: hidden; }
  body {
    background: var(--page);
    font-family: "Open Sans", Arial, sans-serif;
    color: var(--text);
    position: relative;
  }
  .card {
    position: absolute;
    left: 250px;
    width: 700px;
    height: 400px;
    background: var(--card);
    box-shadow: 0 6px 18px rgba(0,0,0,0.18);
    overflow: hidden;
  }
  .card--front { top: 50px; }
  .card--back { top: 500px; }

  .swoosh { position: absolute; inset: 0; width: 100%; height: 100%; }

  .brand {
    position: absolute;
    display: flex;
    align-items: center;
    gap: 12px;
    white-space: nowrap;
  }
  .brand__dot {
    flex: none;
    border-radius: 50%;
    background: var(--green-light);
  }
  .brand__name {
    font-weight: 700;
    color: var(--green-mid);
  }
  .card--front .brand { left: 50px; top: 190px; }
  .card--front .brand__dot { width: 32px; height: 32px; }
  .card--front .brand__name { font-size: 30px; }

  .card--back .brand { left: 330px; top: 160px; flex-direction: column; gap: 16px; }
  .card--back .brand__dot { width: 70px; height: 70px; }
  .card--back .brand__name { font-size: 34px; }

  .contact {
    position: absolute;
    left: 420px;
    top: 42px;
    padding-left: 24px;
    border-left: 1px solid var(--rule);
    height: 190px;
  }
  .contact__name {
    font-weight: 700;
    font-size: 22px;
    color: var(--green-dark);
    margin-bottom: 10px;
  }
  .contact__list { list-style: none; }
  .contact__item {
    display: flex;
    align-items: center;
    gap: 10px;
    font-size: 15px;
    line-height: 27px;
  }
  .icon { width: 16px; height: 16px; flex: none; }
  .icon--square { background: var(--green-dark); border-radius: 2px; width: 14px; height: 14px; margin: 0 1px; }

  .services {
    position: absolute;
    left: 40px;
    right: 40px;
    bottom: 34px;
    display: flex;
    gap: 26px;
    list-style: none;
    font-size: 18px;
    color: var(--text);
  }
  .services__item { display: flex; align-items: center; gap: 8px; white-space: nowrap; }
  .services__item::before {
    content: "";
    width: 10px; height: 10px;
    border-radius: 50%;
    background: var(--green-mid);
  }
</style>
</head>
<body>

<section class="card card--front" aria-label="Card front">
  <svg class="swoosh" viewBox="0 0 700 400" preserveAspectRatio="none" aria-hidden="true">
    <defs>
      <linearGradient id="bandLight" x1="0" y1="0" x2="1" y2="0">
        <stop offset="0" stop-color="#a6d15a"/>
        <stop offset="1" stop-color="#7dbb35"/>
      </linearGradient>
    </defs>
    <path d="M0,352 C300,346 520,320 700,268 L700,284 C520,336 300,362 0,366 Z" fill="#0b6b3a"/>
    <path d="M0,370 C300,366 520,342 700,290 L700,400 L0,400 Z" fill="url(#bandLight)"/>
  </svg>

  <div class="brand">
    <span class="brand__dot"></span>
    <span class="brand__name">Brookvale Yards</span>
  </div>

  <div class="contact">
    <p class="contact__name">Morgan Pell</p>
    <ul class="contact__list">
      <li class="contact__item">
        <svg class="icon" viewBox="0 0 16 16" aria-hidden="true"><path fill="#0b6b3a" d="M3.5 1 6 3.8 4.6 5.6c.9 2 2.6 3.8 4.8 4.8L11.2 9 14 11.5 12.4 14C7 13.6 2.4 9 2 3.6Z"/></svg>
        902-555-0148
      </li>
      <li class="contact__item">
        <svg class="icon" viewBox="0 0 16 16" aria-hidden="true"><rect x="1" y="3" width="14" height="10" rx="1" fill="#0b6b3a"/><path d="M1.5 4 8 9l6.5-5" stroke="#fff" stroke-width="1.3" fill="none"/></svg>
        info@brookvaleyards.ca
      </li>
      <li class="contact__item">
        <svg class="icon" viewBox="0 0 16 16" aria-hidden="true"><circle cx="8" cy="8" r="6.5" fill="none" stroke="#0b6b3a" stroke-width="1.6"/><path d="M1.5 8h13M8 1.5c-3 3.5-3 9.5 0 13M8 1.5c3 3.5 3 9.5 0 13" stroke="#0b6b3a" stroke-width="1.2" fill="none"/></svg>
        brookvaleyards.ca
      </li>
      <li class="contact__item"><span class="icon icon--square"></span>brookvaleyards</li>
      <li class="contact__item"><span class="icon icon--square"></span>brookvaleyard</li>
    </ul>
  </div>
</section>

<section class="card card--back" aria-label="Card back">
  <div class="brand">
    <span class="brand__dot"></span>
    <span class="brand__name">Brookvale Yards</span>
  </div>
  <ul class="services">
    <li class="services__item">Lawn Care</li>
    <li class="services__item">Property Maintenance</li>
    <li class="services__item">Garden Services</li>
  </ul>
</section>

</body>
</html>
```